Stationery and Business Card Design

We need stationary design for our new company lanternfold. Lanternfold is a company that provides city apartment rentals for tourists in Athens We need business cards, letterheads for A4 and A5 and envelopes for A4 A5. The design needs to be modern, friendly and corporate.

Target Market(s)

City Tourists

Industry/Entity Type

Tourism

```html
<!DOCTYPE html>
<html lang="en">
<head>
<meta charset="utf-8">
<title>Lanternfold — Business Card</title>
<link rel="stylesheet" href="https://fonts.googleapis.com/css2?family=Questrial&family=Montserrat:wght@700&display=swap">
<style>
  :root {
    --magenta: #a3195f;
    --magenta-deep: #85124c;
    --magenta-light: #b52f78;
    --slate: #4a4a4c;
    --paper: #f7f7f7;
    --backdrop: #2b2b2d;
    --ink-muted: #555;
  }
  * { margin: 0; padding: 0; box-sizing: border-box; }
  html, body { width: 1200px; height: 900px; overflow: hidden; }
  body {
    background: var(--backdrop);
    font-family: "Questrial", "Helvetica Neue", Arial, sans-serif;
    position: relative;
  }
  .card {
    position: absolute;
    left: 285px;
    width: 630px;
    height: 360px;
    overflow: hidden;
    box-shadow: 0 10px 30px rgba(0,0,0,.45);
  }
  .card--back { top: 45px; background: linear-gradient(120deg, var(--magenta-deep), var(--magenta-light)); }
  .card--front { top: 495px; background: var(--paper); }

  .base-strip {
    position: absolute; left: 0; right: 0; bottom: 0; height: 30px;
    background: var(--slate);
  }

  .brand {
    display: flex; align-items: center; gap: 14px;
    font-family: "Questrial", "Helvetica Neue", Arial, sans-serif;
    letter-spacing: .5px;
  }
  .brand__square { width: 40px; height: 40px; flex: none; }
  .brand__name { font-size: 44px; line-height: 1; }

  .card--back .brand {
    position: absolute; left: 50%; top: 140px; transform: translateX(-50%);
  }
  .card--back .brand__square { background: #fff; }
  .card--back .brand__name { color: #fff; }

  .card--front .brand {
    position: absolute; right: 36px; top: 58px;
  }
  .card--front .brand__square { background: var(--magenta); width: 34px; height: 34px; }
  .card--front .brand__name { color: var(--magenta); font-size: 38px; }

  .contact-band {
    position: absolute; left: 0; right: 0; top: 200px; bottom: 30px;
    background: linear-gradient(110deg, var(--magenta-deep), var(--magenta-light) 55%, var(--magenta-deep));
  }
  .contact-band__notch {
    position: absolute; left: 182px; top: 200px; width: 0; height: 0;
    border-left: 10px solid transparent; border-right: 10px solid transparent;
    border-top: 10px solid var(--paper);
  }

  .person { position: absolute; left: 48px; top: 132px; }
  .person__name {
    font-family: "Montserrat", Arial, sans-serif; font-weight: 700;
    color: var(--magenta); font-size: 19px; letter-spacing: 1px;
  }
  .person__role { color: var(--ink-muted); font-size: 15px; margin-top: 3px; }

  .address {
    position: absolute; right: 36px; top: 222px; text-align: right;
    color: #fff; font-size: 14px; line-height: 1.5;
  }

  .contact-list {
    position: absolute; left: 72px; top: 232px; list-style: none;
    color: rgba(255,255,255,.9); font-size: 14px;
  }
  .contact-list li { display: flex; align-items: center; gap: 10px; height: 22px; }
  .contact-list svg { width: 14px; height: 14px; flex: none; }
</style>
</head>
<body>

  <section class="card card--back" aria-label="Business card, back">
    <div class="brand">
      <span class="brand__square"></span>
      <span class="brand__name">Lanternfold</span>
    </div>
    <div class="base-strip"></div>
  </section>

  <section class="card card--front" aria-label="Business card, front">
    <div class="brand">
      <span class="brand__square"></span>
      <span class="brand__name">Lanternfold</span>
    </div>

    <div class="person">
      <div class="person__name">MAREN KOSTAS</div>
      <div class="person__role">Managing Director</div>
    </div>

    <div class="contact-band"></div>
    <div class="contact-band__notch"></div>

    <div class="address">
      14 Irakleidon Street<br>Athens 118 51
    </div>

    <ul class="contact-list">
      <li>
        <svg viewBox="0 0 14 14" aria-hidden="true"><rect width="14" height="14" rx="2" fill="rgba(255,255,255,.85)"/><path d="M4 3.5l1.6-.4 1 2-1 .8a5 5 0 0 0 2.5 2.5l.8-1 2 1-.4 1.6C7 10.2 3.8 7 4 3.5z" fill="#a3195f"/></svg>
        210-555-0147
      </li>
      <li>
        <svg viewBox="0 0 14 14" aria-hidden="true"><rect width="14" height="14" rx="2" fill="rgba(255,255,255,.85)"/><rect x="3" y="6" width="8" height="4" fill="#a3195f"/><rect x="4.5" y="3" width="5" height="3" fill="#a3195f"/></svg>
        210-555-0193
      </li>
      <li>
        <svg viewBox="0 0 14 14" aria-hidden="true"><rect width="14" height="14" rx="2" fill="rgba(255,255,255,.85)"/><circle cx="7" cy="7" r="4" fill="none" stroke="#a3195f" stroke-width="1"/><path d="M3 7h8M7 3c-2 2.5-2 5.5 0 8M7 3c2 2.5 2 5.5 0 8" fill="none" stroke="#a3195f" stroke-width=".8"/></svg>
        www.lanternfold.com
      </li>
    </ul>

    <div class="base-strip"></div>
  </section>

</body>
</html>
```